8x8 Social Media Ad - Brant Summit Expo

Attention Real Estate Agents
Please join us for our
Quarterly Real Estate Training Expo
The 2nd Saturday of February, May, August and November
Our Next Training Expo is _________________________________
From 9 am to 1 pm
at
Halvorne Suites Millbrook Court
4817 Copper Willow Lane, Dunmere, MD 20588
Scheduled Speakers
9:00 am - Marcus Pellington - Orientation
9:30 am - Derrin Oakfield - Multiple Income Streams / Crest Program
10:00 am - Talia Brennick - Marketing though Social Media
10:45 am - Rex Dunmore - Generating Business through Ru-Plaza
11:30 am - Kemi Adeyoro - Real Estate Investing
12:15 pm - Gregor Tamsey - (Main Speaker) Training Topic TBA
For more information call Marcus Pellington at (240) 555-0183 or email mpellington@brantsummithomes.example

```html
<!DOCTYPE html>
<html lang="en">
<head>
<meta charset="utf-8">
<title>Brant Summit Expo – Quarterly Training</title>
<link rel="stylesheet" href="https://fonts.googleapis.com/css2?family=Montserrat:wght@400;500;600;700&family=Mrs+Saint+Delafield&display=swap">
<style>
  :root {
    --teal: #1e8f98;
    --teal-band: #2a969e;
    --ink: #2b2b2b;
    --bg-top: #f4f5f5;
    --bg-mid: #dadcdc;
    --bg-low: #b9bcbd;
    --white: #ffffff;
  }
  * { margin: 0; padding: 0; box-sizing: border-box; }
  html, body { width: 1200px; height: 1200px; overflow: hidden; }
  body { font-family: "Montserrat", sans-serif; color: var(--ink); }
  .ad {
    position: relative; width: 1200px; height: 1200px; overflow: hidden;
  }
  .city-backdrop {
    position: absolute; inset: 0;
    background: linear-gradient(180deg, var(--bg-top) 0%, #e9eaea 30%, var(--bg-mid) 60%, var(--bg-low) 100%);
  }
  .brand {
    position: absolute; top: 62px; left: 0; width: 100%;
    display: flex; justify-content: center; align-items: center; gap: 12px;
  }
  .brand-mark { width: 22px; height: 22px; background: var(--teal); }
  .brand-name { font-weight: 700; font-size: 24px; color: var(--teal); letter-spacing: 0.5px; text-transform: uppercase; }
  .headline { position: absolute; top: 190px; left: 0; width: 100%; text-align: center; }
  .headline-script {
    font-family: "Mrs Saint Delafield", cursive; font-size: 96px; line-height: 1;
    color: var(--ink); height: 80px;
  }
  .headline-main {
    font-weight: 700; font-size: 70px; line-height: 1; color: var(--teal);
    letter-spacing: 1px; margin-top: -6px;
  }
  .headline-sub { font-weight: 700; font-size: 40px; color: var(--ink); margin-top: 8px; letter-spacing: 1px; }
  .invite {
    position: absolute; top: 397px; left: 0; width: 100%; text-align: center;
    font-size: 21px; line-height: 30px; text-transform: uppercase; font-weight: 400;
  }
  .speakers {
    position: absolute; top: 488px; left: 49px; width: 1102px;
    display: flex; justify-content: space-between;
  }
  .speaker { width: 170px; }
  .speaker-photo {
    position: relative; height: 295px;
  }
  .speaker-photo .panel { position: absolute; left: 0; right: 0; top: 50px; bottom: 0; background: var(--teal); }
  .speaker-photo .portrait {
    position: absolute; left: 18px; right: 18px; top: 0; bottom: 0;
    background: linear-gradient(180deg, #5b4a40 0%, #3a3536 45%, #2a3550 100%);
    border-radius: 60px 60px 0 0;
  }
  .speaker-info { margin-top: 20px; font-size: 14px; line-height: 18px; text-transform: uppercase; letter-spacing: 0.3px; }
  .speaker-name { color: var(--teal); font-weight: 700; }
  .schedule-note {
    position: absolute; top: 938px; left: 0; width: 100%; text-align: center;
    font-weight: 700; font-size: 21px; text-transform: uppercase;
  }
  .venue-band {
    position: absolute; top: 974px; left: 0; width: 100%; height: 116px;
    background: var(--teal-band); color: var(--white);
    display: flex; flex-direction: column; justify-content: center; align-items: center;
    font-size: 22px; line-height: 28px; text-transform: uppercase; font-weight: 500;
  }
  .contact {
    position: absolute; top: 1124px; left: 0; width: 100%;
    display: flex; justify-content: center; gap: 38px; font-size: 22px; text-transform: uppercase;
  }
  .contact-item { display: flex; align-items: center; gap: 16px; }
  .contact-item svg { fill: var(--teal); }
</style>
</head>
<body>
<main class="ad">
  <div class="city-backdrop" role="img" aria-label="Hazy downtown skyline of high-rise towers"></div>

  <header class="brand">
    <span class="brand-mark"></span>
    <span class="brand-name">Brant Summit Luxury Realty</span>
  </header>

  <section class="headline">
    <div class="headline-script">Attention</div>
    <h1 class="headline-main">REAL STATE</h1>
    <h2 class="headline-sub">AGENTS</h2>
  </section>

  <p class="invite">Please join us for our<br>Quarterly Real Estate Training Expo</p>

  <section class="speakers">
    <article class="speaker">
      <div class="speaker-photo"><div class="panel"></div><div class="portrait" role="img" aria-label="Portrait of Derrin Oakfield"></div></div>
      <div class="speaker-info"><div>9:30 AM</div><div class="speaker-name">Derrin Oakfield</div><div>Multiple Income/ Streams / Crest-Program</div></div>
    </article>
    <article class="speaker">
      <div class="speaker-photo"><div class="panel"></div><div class="portrait" role="img" aria-label="Portrait of Marcus Pellington"></div></div>
      <div class="speaker-info"><div>9:00 AM</div><div class="speaker-name">Marcus Pellington</div><div>Orientation</div></div>
    </article>
    <article class="speaker">
      <div class="speaker-photo"><div class="panel"></div><div class="portrait" role="img" aria-label="Portrait of Talia Brennick"></div></div>
      <div class="speaker-info"><div>10:00 AM</div><div class="speaker-name">Talia Brennick</div><div>Marketing though Social Media</div></div>
    </article>
    <article class="speaker">
      <div class="speaker-photo"><div class="panel"></div><div class="portrait" role="img" aria-label="Portrait of Rex Dunmore"></div></div>
      <div class="speaker-info"><div>10:45 AM</div><div class="speaker-name">Rex Dunmore</div><div>Generating Business through Ru-Plaza</div></div>
    </article>
    <article class="speaker">
      <div class="speaker-photo"><div class="panel"></div><div class="portrait" role="img" aria-label="Portrait of Kemi Adeyoro"></div></div>
      <div class="speaker-info"><div>11:30 AM</div><div class="speaker-name">Kemi Adeyoro</div><div>Real Estate Investing</div></div>
    </article>
    <article class="speaker">
      <div class="speaker-photo"><div class="panel"></div><div class="portrait" role="img" aria-label="Portrait of Gregor Tamsey"></div></div>
      <div class="speaker-info"><div>12:15 PM</div><div class="speaker-name">Gregor Tamsey</div><div>(Main Speaker) Training Topic TBA</div></div>
    </article>
  </section>

  <p class="schedule-note">The 2nd Saturday of February, May, August and November</p>

  <section class="venue-band">
    <div>Our next training expo is from 9 AM to 1 PM at</div>
    <div>Halvorne Suites Millbrook Court</div>
    <div>4817 Copper Willow Lane, Dunmere, MD 20588</div>
  </section>

  <footer class="contact">
    <div class="contact-item">
      <svg width="20" height="20" viewBox="0 0 24 24" aria-hidden="true"><path d="M6.6 10.8a15.1 15.1 0 0 0 6.6 6.6l2.2-2.2a1 1 0 0 1 1-.25 11.4 11.4 0 0 0 3.6.57 1 1 0 0 1 1 1V20a1 1 0 0 1-1 1A17 17 0 0 1 3 4a1 1 0 0 1 1-1h3.5a1 1 0 0 1 1 1c0 1.25.2 2.45.57 3.57a1 1 0 0 1-.25 1z"/></svg>
      <span>240-555-0183</span>
    </div>
    <div class="contact-item">
      <svg width="22" height="18" viewBox="0 0 24 20" aria-hidden="true"><path d="M2 2h20a1 1 0 0 1 1 1v.5l-11 7-11-7V3a1 1 0 0 1 1-1zm-1 4 11 7 11-7v11a1 1 0 0 1-1 1H2a1 1 0 0 1-1-1z"/></svg>
      <span>mpellington@brantsummithomes.example</span>
    </div>
  </footer>
</main>
</body>
</html>
```